New Business Card Design for Manufacturing

We are an engineering/manufacturing company that offers Advanced machining/assembly/engineering services, as well as innovative products for the heavy duty engine cooling markets.

We are looking to get a new business card designed that is clean and modern looking, but still fits the wide range of technical/skilled work we do.

- We hope to use this design as the base for other design work in new Presentations, web, and print work.

Industry/Entity Type

Engineering

Contact Information for Business Card

Our preferred color of blue is (RGB) 22/71/159 but can vary slightly from that color. Our content will be our Logo and full company name (Vantrell Forge Works, Inc.), company address, name, job title, phone number with extension, cell number, fax number, website, and email address on the cards.
We'd like the full company name next to the logo, but we are open to other interpretations of that layout.
Preferably, we would like the back side to be clean with just our logo, and the front to contain all of the contact information.

Colors
2f74b4
0355a3
85abd2

Requirements
Must have
• - Logo, company name, needed content - We are open to interpretation beyond that.
• - Standard size business card.
• - Horizontal orientation.
• - Enough space for lengthy names / job titles (for example, a job title could read "Directory of Human Resources" or "V.P. of Governmental Affairs"). We need this to look clean, whether the title be short (CEO) or long (as described above).

```html
<!DOCTYPE html>
<html lang="en">
<head>
<meta charset="utf-8">
<title>Vantrell Forge Works – Business Card</title>
<link href="https://fonts.googleapis.com/css2?family=Fira+Sans:wght@400;500;600&display=swap" rel="stylesheet">
<style>
  :root {
    --page: #e9e9e9;
    --card-black: #0b0b0c;
    --brand-blue: #0355a3;
    --brand-blue-deep: #03468c;
    --brand-blue-light: #85abd2;
    --paper: #f3f3f3;
    --white: #ffffff;
    --soft-white: #e6eef7;
  }
  * { margin: 0; padding: 0; box-sizing: border-box; }
  html, body {
    width: 1200px; height: 576px; overflow: hidden;
    background: var(--page);
    font-family: "Fira Sans", Arial, sans-serif;
  }
  .stage { position: relative; width: 1200px; height: 576px; }
  .card {
    position: absolute; top: 138px;
    width: 484px; height: 294px;
    border-radius: 14px; overflow: hidden;
  }
  .card--back { left: 80px; background: var(--card-black);
    display: flex; align-items: center; justify-content: center; }
  .back-name {
    color: var(--white); font-weight: 600; font-size: 34px;
    letter-spacing: 0.5px; text-align: center; line-height: 1.1;
  }
  .card--front { left: 604px; background: var(--paper); }
  .front-shape { position: absolute; inset: 0; }
  .front-brand {
    position: absolute; left: 72px; top: 147px;
    transform: translate(-50%, -50%) rotate(-90deg);
    white-space: nowrap;
    color: var(--brand-blue); font-weight: 600; font-size: 22px;
  }
  .details { position: absolute; left: 230px; top: 28px; color: var(--white); }
  .person-name { font-size: 19px; font-weight: 500; line-height: 24px; }
  .person-title { font-size: 11.5px; line-height: 15px; }
  .company { font-size: 12.5px; font-weight: 600; margin-top: 42px; }
  .contact-list { list-style: none; margin-top: 6px; }
  .contact-list li {
    display: flex; align-items: center; gap: 8px;
    font-size: 11.5px; line-height: 16.5px;
  }
  .contact-list svg { width: 10px; height: 10px; fill: var(--white); flex: none; }
  .address { font-size: 11.5px; line-height: 16px; margin-top: 6px; }
</style>
</head>
<body>
<div class="stage">
  <section class="card card--back">
    <p class="back-name">Vantrell Forge Works</p>
  </section>

  <section class="card card--front">
    <svg class="front-shape" viewBox="0 0 484 294" preserveAspectRatio="none">
      <defs>
        <linearGradient id="panelBlue" x1="0" y1="0" x2="1" y2="1">
          <stop offset="0" stop-color="#0355a3"/>
          <stop offset="1" stop-color="#03468c"/>
        </linearGradient>
      </defs>
      <path d="M150 0 Q 200 150 160 294 L484 294 L484 0 Z" fill="#85abd2"/>
      <path d="M158 0 Q 208 150 168 294 L484 294 L484 0 Z" fill="url(#panelBlue)"/>
    </svg>
    <p class="front-brand">Vantrell Forge Works</p>

    <div class="details">
      <h1 class="person-name">Marcus Elden Hale</h1>
      <p class="person-title">Managing Director</p>
      <p class="company">Vantrell Forge Works, Inc.</p>
      <ul class="contact-list">
        <li><svg viewBox="0 0 10 10"><path d="M1 3 Q5 0 9 3 L8 4.5 L6.5 4 L6.5 3 Q5 2.5 3.5 3 L3.5 4 L2 4.5 Z M2.5 5 L7.5 5 L8.5 9 L1.5 9 Z"/></svg>555-0142-7700 (VFW)</li>
        <li><svg viewBox="0 0 10 10"><path d="M2.5 0.5 H7.5 V9.5 H2.5 Z M3.3 1.5 V7.5 H6.7 V1.5 Z"/></svg>555-0178-3361</li>
        <li><svg viewBox="0 0 10 10"><path d="M3 0.5 H7 V3 H3 Z M1 3.5 H9 V7.5 H7.5 V6 H2.5 V7.5 H1 Z M3 6.5 H7 V9.5 H3 Z"/></svg>555-0190-2284</li>
        <li><svg viewBox="0 0 10 10"><path d="M0.5 2 H9.5 V8 H0.5 Z M1.2 2.6 L5 5.5 L8.8 2.6 Z" fill-rule="evenodd"/></svg>www.vantrellforge.com</li>
        <li><svg viewBox="0 0 10 10"><path d="M5 0.5 A4.5 4.5 0 1 0 5.01 0.5 Z M5 1.5 A3.5 3.5 0 1 1 4.99 1.5 Z M1.5 4.6 H8.5 V5.4 H1.5 Z M4.6 1.5 H5.4 V8.5 H4.6 Z" fill-rule="evenodd"/></svg>m.hale@vantrellforge.com</li>
      </ul>
      <p class="address">418 Millbrook Rd., Carver Falls,<br>Ridgeton, US 204817</p>
    </div>
  </section>
</div>
</body>
</html>
```